Visitenkarten/Briefpaier/Kassenkassenbelege für Juwelier
Zielgruppe
Mittelständischer Juwelier mit zwei Filialen. Klassischer Schmuck, Uhren und Modeschmuck
Aufgabenstellung
Es müssen für zwei Geschäfte Visitenkarten, Briefpapier (A4) und Kassenkassenbelege (A6) erstellt werden. Logo und Typo im Anhang. Ein Farbkonzept besteht noch nicht. Die Idee geht in Richtung Bordeaux-Rot.
Generell:
(1) Sieht erstmal nach viel Beschreibung aus, bitte nicht entmutigen lassen, sind zu 90% nur austauschbare Inhalts-/Kontaktdaten.
(2) Für meine Zwecke reicht es vollkommen aus, wenn bei den Vorschlägen zur Arbeitsersparnis erstmal nur mit einer Adresse gearbeitet wird. Wenn ich dann den zutreffenden Designvorschlag gefunden habe, können wir die zweite Adresse in dem ersten Format umsetzen. Ich denke das spart Zeit und Nerven.
(3) Bitte Angaben wie "Tel.:" oder "USt.- ID:" nicht wörtlich nehmen, es soll dabei klar sein worum es geht; wenn "Telefon" ausgeschrieben besser aussieht, bitte in der optisch ansprechenderen Form verwenden.
(4) Bei Fragen, bitte fragen!
(5) Viel Spass bei dem Projekt - Ich freu' mich auf die Vorschläge!
Visitenkarten(1):
Juwelier Brenneck GmbH
www.juwelier-brenneck-beispiel.de
Visitenkarten(2):
Visitenkarten(generell):
(1) Die einzelnen Daten können durch Hervorhebungen wie Adresse, Kontakt, Online/Internet unterteilt bzw. hervorgehoben werden.
(2) Die Visitenkarten sollen farbig gedruckt werden; geplant ist weiß als Hintergrund ist aber nicht zwingend bei einer guten anderen Idee
Briefpapier:
(1)Absender im Adressfeld für DIN-lang Briefumschläge mit Fenster:
(2)Informationen im Footer/Seitenbereich:
Juwelier Brenneck Gmb..

```html
<!DOCTYPE html>
<html lang="de">
<head>
<meta charset="utf-8">
<title>Juwelier Brenneck – Visitenkarte</title>
<link rel="stylesheet" href="https://fonts.googleapis.com/css2?family=Source+Sans+3:wght@400;600;700&display=swap">
<style>
  :root {
    --bordeaux: #9b1118;
    --bordeaux-deep: #7e0c12;
    --paper: #ffffff;
    --stage: #e9e4e2;
    --ink-light: #ffffff;
  }
  * { box-sizing: border-box; margin: 0; padding: 0; }
  html, body { width: 1200px; height: 1200px; overflow: hidden; }
  body {
    background: var(--stage);
    font-family: "Source Sans 3", sans-serif;
    display: flex;
    flex-direction: column;
    align-items: center;
    justify-content: center;
    gap: 64px;
  }
  .card {
    width: 800px;
    height: 513px;
    position: relative;
    overflow: hidden;
    box-shadow: 0 6px 18px rgba(60, 10, 14, 0.18);
  }

  /* Vorderseite */
  .card--front {
    background: var(--bordeaux);
    display: flex;
    flex-direction: column;
    align-items: center;
    justify-content: center;
    gap: 26px;
    color: var(--ink-light);
  }
  .brand-mark {
    width: 64px;
    height: 64px;
    background: var(--paper);
  }
  .brand-name {
    font-weight: 700;
    font-size: 58px;
    letter-spacing: 3px;
    text-transform: uppercase;
    line-height: 1;
  }

  /* Rückseite */
  .card--back { display: flex; }
  .back-info {
    width: 56%;
    background: var(--paper);
    color: var(--bordeaux);
    display: flex;
    flex-direction: column;
    align-items: center;
    padding-top: 70px;
  }
  .back-info .brand-mark {
    width: 40px;
    height: 40px;
    background: var(--bordeaux);
    margin-bottom: 20px;
  }
  .back-info .brand-name {
    font-size: 36px;
    letter-spacing: 2px;
  }
  .brand-rule {
    width: 300px;
    height: 2px;
    background: var(--bordeaux);
    margin-top: 16px;
  }
  .address {
    font-style: normal;
    font-size: 22px;
    line-height: 1.4;
    text-align: center;
    margin-top: 70px;
  }
  .back-contact {
    width: 44%;
    background: var(--bordeaux);
    color: var(--ink-light);
    display: flex;
    flex-direction: column;
    justify-content: center;
    padding: 0 30px 0 34px;
    font-size: 21px;
    line-height: 1.4;
  }
  .contact-phone { margin-top: 40px; }
  .contact-online { margin-top: 70px; }
</style>
</head>
<body>
  <section class="card card--front" aria-label="Visitenkarte Vorderseite">
    <div class="brand-mark" aria-hidden="true"></div>
    <p class="brand-name">Juwelier Brenneck</p>
  </section>

  <section class="card card--back" aria-label="Visitenkarte Rückseite">
    <div class="back-info">
      <div class="brand-mark" aria-hidden="true"></div>
      <p class="brand-name">Juwelier Brenneck</p>
      <div class="brand-rule" aria-hidden="true"></div>
      <address class="address">
        Juwelier Brenneck GmbH<br>
        Goldschmiedegasse 12<br>
        45127 Musterstadt
      </address>
    </div>
    <div class="back-contact">
      <p class="contact-phone">Tel.: 01 23 - 45 67 89<br>Fax: 01 23 - 45 67 90</p>
      <p class="contact-online">info@juwelier-brenneck-beispiel.de<br>www.juwelier-brenneck-beispiel.de</p>
    </div>
  </section>
</body>
</html>
```